New Business Card Design Project

Need a design that will create an impact / strong impression towards our clients for our business. We are in the lighting business and we do lighting retrofits for large commercial to industrial clientele.

Target Market(s)

Lighting Industry

Industry/Entity Type

Business

Font styles to use
Other font styles liked:
• we would like to use the font on our logo, not sure what it is though..

Requirements
Must have
• Our logo.
Nice to have
• We are open to suggestions that have to do with lighting.

```html
<!DOCTYPE html>
<html lang="en">
<head>
<meta charset="utf-8">
<title>Lumenra Retrofit Co. — Business Card</title>
<link href="https://fonts.googleapis.com/css2?family=Montserrat:wght@600;700&family=Open+Sans:wght@400;600&display=swap" rel="stylesheet">
<style>
  :root {
    --backdrop: #3a332f;
    --card: #121212;
    --card-edge: #1c1c1c;
    --green: #1f9a3e;
    --green-bright: #3cc25e;
    --text: #f2f2f2;
    --silver: #c9c9c9;
  }
  * { margin: 0; padding: 0; box-sizing: border-box; }
  html, body {
    width: 1200px; height: 900px; overflow: hidden;
    background: var(--backdrop);
  }
  .canvas {
    position: relative; width: 1200px; height: 900px;
  }
  .card {
    position: absolute; top: 300px;
    width: 520px; height: 300px;
    background: var(--card);
    border: 1px solid var(--card-edge);
    box-shadow: 0 18px 40px rgba(0,0,0,.45);
  }
  .card--front { left: 50px; }
  .card--back { left: 630px; }

  .brand {
    position: absolute;
    font-family: "Montserrat", sans-serif;
    font-weight: 700;
    letter-spacing: 1px;
    display: flex; align-items: center; gap: 10px;
    white-space: nowrap;
  }
  .brand__mark { width: 14px; height: 14px; }
  .card--front .brand {
    top: 62px; left: 50%; transform: translateX(-50%);
    color: var(--green); font-size: 26px;
  }
  .card--front .brand__mark { background: var(--green); }
  .card--back .brand {
    top: 50%; left: 50%; transform: translate(-50%, -50%);
    color: var(--silver); font-size: 30px;
  }
  .card--back .brand__mark { background: var(--silver); }

  .holder {
    position: absolute; left: 40px; top: 176px;
    font-family: "Open Sans", sans-serif; color: var(--text);
  }
  .holder__name {
    font-family: "Montserrat", sans-serif; font-weight: 700;
    color: var(--green-bright); font-size: 18px; letter-spacing: .5px;
  }
  .holder__role { font-size: 14px; margin-bottom: 8px; }
  .contact { list-style: none; font-size: 14px; line-height: 20px; }
  .contact li { display: flex; align-items: center; gap: 8px; }
  .contact svg { width: 11px; height: 11px; fill: var(--green-bright); }

  .address {
    position: absolute; right: 40px; top: 140px;
    font-family: "Open Sans", sans-serif; color: var(--text);
    font-size: 14px; line-height: 20px; text-align: right;
  }
</style>
</head>
<body>
<main class="canvas">
  <section class="card card--front" aria-label="Card front">
    <div class="brand"><span class="brand__mark"></span>LUMENRA RETROFIT CO.</div>

    <address class="address">1234, Address GoesHere,<br>Country name, 12345</address>

    <div class="holder">
      <div class="holder__name">JONATHAN SMITH</div>
      <div class="holder__role">Managing Director</div>
      <ul class="contact">
        <li>
          <svg viewBox="0 0 12 12"><path d="M2.5 0.5l2 2.5-1.2 1.3c.7 1.6 2 2.9 3.5 3.6l1.3-1.2 2.4 2-1.2 2.3C5 10.7 1 6.8.2 1.6z"/></svg>
          (044)123456789
        </li>
        <li>
          <svg viewBox="0 0 12 12"><path d="M0 2h12v8H0z M0 2l6 4.5L12 2" stroke="#121212" stroke-width=".9"/></svg>
          info@youremail.com
        </li>
        <li>
          <svg viewBox="0 0 12 12"><circle cx="6" cy="6" r="5.5"/><path d="M.5 6h11M6 .5c-3 3-3 8 0 11M6 .5c3 3 3 8 0 11" stroke="#121212" stroke-width=".8" fill="none"/></svg>
          www.websitename.com
        </li>
      </ul>
    </div>
  </section>

  <section class="card card--back" aria-label="Card back">
    <div class="brand"><span class="brand__mark"></span>LUMENRA RETROFIT CO.</div>
  </section>
</main>
</body>
</html>
```